Yacht, Boats, Watersports company needs a redesign of business card

Hello Designers!
We are a Boat dealership company that sells fun in the water, we sell boats, Yachts, Kayaks and also yacht WaterSport toys. We are looking to redesign our business cards in to something a little bit more sophisticated. in a way that we can make better use of our company colors. I'm attaching a zipped file containing the company 3 sets of company logo which one is an horizontal another one is a vertical and also a chromed 3d logo. Also is included two set of business cards that we use and also some designs that i think it's interesting. We use PMS 2026c Orange and PMS 7687C Blue. I would like to see at least two different options with the orange as accent and also using blue as an accent color. It's really important for the business cards to have a font option and size that is legible to most people. Our current website is wwww.coralpennant.com. Please visit if you want to have a better feeling of the Boat dealership
You can send Single sided or double side options. We are now using single sided but we may be open for a double side option if we really like the design.
Target Market(s)
Marine, boat sales, yacht sales, water toys sales/
Contact Information for Business Card
Name: Dale Whitcombe
Address: 212 North Fenwick Lane,
Harbor Point, FL 33019
Phone: 954-731-8842
Fax: 954:731-8843
Cell: 954-382-1490
Email: dw@coralpennant.com
Website: coralpennant.com
Requirements
Must have
- the current information of the business card provided.
logo
use the PMS Colors
Nice to have
- a touch of elegance and sophistication but simple
Should not have
- should not have any typography that is hard to read, the card should be simple but yet sophisticated.

```html
<!DOCTYPE html>
<html lang="en">
<head>
<meta charset="utf-8">
<title>Coral Pennant – Business Card</title>
<link rel="stylesheet" href="https://fonts.googleapis.com/css2?family=Montserrat:wght@600;700&family=Work+Sans:wght@400;500&display=swap">
<style>
  :root {
    --brand-orange: #ef6131;
    --brand-blue: #17467a;
    --paper-white: #ffffff;
    --backdrop: #1e1e1e;
  }
  html, body {
    margin: 0;
    width: 1200px;
    height: 900px;
    overflow: hidden;
    background: var(--backdrop);
  }
  .stage {
    position: relative;
    width: 1200px;
    height: 900px;
  }
  .card {
    position: absolute;
    left: 300px;
    width: 600px;
    height: 343px;
    overflow: hidden;
    box-shadow: 0 10px 30px rgba(0,0,0,.5);
  }
  .card--front { top: 87px; background: var(--brand-orange); }
  .card--back  { top: 470px; background: var(--brand-blue); }

  .card__band {
    position: absolute;
    left: 0; right: 0; bottom: 0;
  }
  .card--front .card__band {
    height: 20px;
    background: var(--brand-blue);
    border-top: 2px solid var(--paper-white);
    box-shadow: 0 -4px 0 var(--brand-blue);
  }
  .card--back .card__band {
    height: 24px;
    background: var(--brand-orange);
    border-top: 2px solid var(--paper-white);
    box-shadow: 0 -4px 0 var(--brand-orange);
  }

  .brand {
    position: absolute;
    display: flex;
    flex-direction: column;
    align-items: center;
    gap: 12px;
  }
  .brand__dot {
    width: 50px; height: 50px;
    border-radius: 50%;
    border: 5px solid currentColor;
    box-sizing: border-box;
  }
  .brand__name {
    font-family: "Montserrat", sans-serif;
    font-weight: 700;
    font-size: 25px;
    letter-spacing: 2px;
    text-transform: uppercase;
    white-space: nowrap;
  }
  .card--front .brand {
    left: 0; right: 0; top: 95px;
    color: var(--brand-blue);
  }
  .card--back .brand {
    left: 38px; width: 250px; top: 102px;
    color: var(--paper-white);
  }
  .card--back .brand__name { font-size: 21px; }
  .card--back .brand__dot { color: var(--brand-orange); }

  .divider {
    position: absolute;
    left: 308px; top: 62px;
    width: 2px; height: 200px;
    background: var(--brand-orange);
  }
  .contact {
    position: absolute;
    left: 332px; top: 60px;
    right: 20px;
    color: var(--paper-white);
    font-family: "Work Sans", sans-serif;
    font-size: 14.5px;
    line-height: 1.4;
    letter-spacing: .6px;
  }
  .contact__name {
    margin: 0 0 8px;
    font-family: "Montserrat", sans-serif;
    font-weight: 700;
    font-size: 21px;
    letter-spacing: 2.2px;
    color: var(--brand-orange);
    text-transform: uppercase;
    white-space: nowrap;
  }
  .contact__address { margin: 0 0 6px; font-style: normal; }
  .contact__list { list-style: none; margin: 0; padding: 0; }
  .contact__list li { display: flex; align-items: center; gap: 8px; }
  .contact__icon { width: 12px; height: 12px; flex: none; color: var(--brand-orange); }
</style>
</head>
<body>
<main class="stage">
  <section class="card card--front" aria-label="Card front">
    <div class="brand">
      <span class="brand__dot"></span>
      <span class="brand__name">Coral Pennant</span>
    </div>
    <div class="card__band"></div>
  </section>

  <section class="card card--back" aria-label="Card back">
    <div class="brand">
      <span class="brand__dot"></span>
      <span class="brand__name">Coral Pennant</span>
    </div>
    <div class="divider"></div>
    <div class="contact">
      <h1 class="contact__name">Dale Whitcombe</h1>
      <address class="contact__address">212 North Fenwick Lane,<br>Harbor Point, FL 33019</address>
      <ul class="contact__list">
        <li>
          <svg class="contact__icon" viewBox="0 0 12 12"><path d="M2.5 1h2l1 2.5-1.3 1a6 6 0 0 0 3.3 3.3l1-1.3L11 7.5v2A1.5 1.5 0 0 1 9.5 11 8.5 8.5 0 0 1 1 2.5 1.5 1.5 0 0 1 2.5 1z" fill="currentColor"/></svg>
          954-731-8842
        </li>
        <li>
          <svg class="contact__icon" viewBox="0 0 12 12"><rect x="3" y="1" width="6" height="3" fill="currentColor"/><rect x="1" y="4.5" width="10" height="4.5" rx="1" fill="currentColor"/><rect x="3" y="8" width="6" height="3" fill="currentColor"/></svg>
          954:731-8843
        </li>
        <li>
          <svg class="contact__icon" viewBox="0 0 12 12"><rect x="3" y="0.8" width="6" height="10.4" rx="1" fill="none" stroke="currentColor" stroke-width="1.2"/><circle cx="6" cy="9.3" r=".7" fill="currentColor"/></svg>
          954-382-1490
        </li>
        <li>
          <svg class="contact__icon" viewBox="0 0 12 12"><rect x="0.8" y="2.3" width="10.4" height="7.4" fill="none" stroke="currentColor" stroke-width="1.1"/><path d="M1 2.6 6 6.6l5-4" fill="none" stroke="currentColor" stroke-width="1.1"/></svg>
          dw@coralpennant.com
        </li>
        <li>
          <svg class="contact__icon" viewBox="0 0 12 12" fill="none" stroke="currentColor" stroke-width="1"><circle cx="6" cy="6" r="5"/><ellipse cx="6" cy="6" rx="2.2" ry="5"/><path d="M1 6h10M2 3.5h8M2 8.5h8"/></svg>
          www.coralpennant.com
        </li>
      </ul>
    </div>
    <div class="card__band"></div>
  </section>
</main>
</body>
</html>
```